Flyer-Design für Ofenservice Firma
Zielgruppe
Die Firma hat als Kerngeschäft Wartung, Reinigung, Reparatur und Inbetriebnahme von Öfen und Kaminen aller Art. Der Fokus liegt dabei auf Pelletöfen. Die Firma versteht sich als zuverlässiger Dienstleister mit gutem Preisleistungsverhältnis. Zielgruppe sind hauptsächlich private Bewohner von Einfamilienhäusern in der ländlichen Gegend (Hessen)
Aufgabenstellung
Zur Bekanntmachung nach Neugründung soll ein Faltflyer gestaltet werden mit insgesamt 6 Bereichen. Die Informationen, welche auf den Flyer sollen, entnehmen Sie bitte dem Entwurf (flyer.pdf). Dieser stellt nur eine erste Idee dar und darf gerne nach Belieben verändert bzw. neu gestaltet werden. Die enthaltenen Informationen, sollten im Großen und Ganzen aber beibehalten werden. Schön wäre evtl. auch eine Hervorhebung der Preise, da wir Preisführer im Markt sind. Auch die Bilder unseres Teams sollen in den Flyer integriert sein. Auf Anfrage kann ich auch gerne weitere Kamin- und Ofenfotos zur Verfügung stellen, für welche ich die Nutzungsrechte habe. Falls Sie weitere Informationen benötigen oder Fragen haben, kommen Sie gerne auf mich zu. Die Bilder dürfen gerne etwas ausgeschnitten werden. Es geht in erster Linie darum, dass die Kunden erkennen, welche Art von Ofen sie zu Hause haben.

```html
<!DOCTYPE html>
<html lang="de">
<head>
<meta charset="utf-8">
<title>KALORA Ofenservice – Faltflyer</title>
<link href="https://fonts.googleapis.com/css2?family=Open+Sans:wght@400;600;700&display=swap" rel="stylesheet">
<style>
:root{
  --backdrop:#5b4b44;
  --paper:#ffffff;
  --paper-soft:#eceded;
  --panel-grey:#c8c9ca;
  --orange:#d2622a;
  --ink:#45474a;
  --ink-soft:#5d6064;
  --photo-warm-a:#3a2f2a;
  --photo-warm-b:#b6865a;
  --photo-cool-a:#8d9093;
  --photo-cool-b:#e3e3e1;
}
*{box-sizing:border-box;margin:0;padding:0}
html,body{width:685px;height:1200px;overflow:hidden}
body{background:var(--backdrop);font-family:"Open Sans",Arial,sans-serif;color:var(--ink);position:relative}
.spread{position:absolute;left:20px;width:645px;height:250px;display:flex;box-shadow:0 6px 18px rgba(0,0,0,.35)}
.spread--outside{top:300px}
.spread--inside{top:650px}
.panel{position:relative;width:215px;height:250px;overflow:hidden;background:var(--paper)}
.panel + .panel{border-left:1px solid rgba(0,0,0,.08)}
.photo{position:absolute;left:0;top:0;width:100%;height:92px}
.photo--fire{background:linear-gradient(135deg,var(--photo-warm-a),#6b5240 55%,var(--photo-warm-b))}
.photo--pellet{background:linear-gradient(120deg,var(--photo-cool-a),var(--photo-cool-b))}
.photo--room{background:linear-gradient(110deg,#d9d4cc,#8b6a50 60%,#3a302b)}
.photo--modern{background:linear-gradient(120deg,#1f2226,#4a4640 55%,#a78a66)}
.photo--team{top:auto;bottom:0;height:92px;background:linear-gradient(180deg,rgba(200,201,202,0),#5a5c60 45%,#2c2e31)}
.tab{position:absolute;left:0;top:84px;background:var(--paper);color:var(--orange);font-size:7px;font-weight:700;padding:3px 10px 3px 8px;border-bottom:2px solid var(--orange)}
.grey-area{position:absolute;left:0;right:0;bottom:0;background:var(--panel-grey)}
.copy{font-size:5.6px;line-height:1.5;color:var(--ink)}
.copy strong{font-weight:700}
.copy p + p{margin-top:5px}
.list{list-style:none}
.list li::before{content:"· "}
.contact{position:absolute;left:0;right:0;top:30px;text-align:center}
.contact__address{font-size:6.5px;font-weight:700;line-height:1.4}
.contact__phone{font-size:9px;font-weight:700;color:var(--orange);margin-top:3px}
.brand{position:absolute;left:20px;top:20px;display:flex;align-items:center;gap:6px}
.brand__mark{width:12px;height:12px;background:var(--orange)}
.brand__name{font-size:15px;font-weight:700;letter-spacing:1px;color:var(--ink)}
.brand__sub{position:absolute;left:38px;top:40px;font-size:6.5px;color:var(--ink-soft)}
.cover-curve{position:absolute;left:0;top:0;width:215px;height:250px}
.headline{position:absolute;left:20px;top:70px;font-size:8.5px;font-weight:700;line-height:1.3;color:var(--orange)}
.bullets{position:absolute;left:20px;top:98px;font-size:5.8px;line-height:1.6;color:var(--ink)}
.offer{position:absolute;left:0;right:0;bottom:0;height:36px;background:var(--orange);color:#fff;text-align:center;padding-top:5px}
.offer__title{font-size:7px;font-weight:700}
.offer__text{font-size:7px}
.offer__note{font-size:4.8px}
.type-tags{position:absolute;left:0;top:8px;display:flex;flex-direction:column;gap:5px}
.type-tags span{background:var(--paper);color:var(--orange);font-size:6px;font-weight:700;padding:2px 8px}
</style>
</head>
<body>

<section class="spread spread--outside" aria-label="Außenseite">
  <div class="panel panel--services">
    <div class="photo photo--fire" role="img" aria-label="Foto: Kaminofen mit Feuer in einem Wohnraum"></div>
    <div class="tab">Weitere Leistungen</div>
    <div class="grey-area" style="top:104px;padding:12px 14px">
      <div class="copy">
        <p><strong>Reparatur und Instandsetzung:</strong><br>Funktioniert Ihr Ofen nicht richtig, sind wir schnellstmöglich für Sie da und setzen Ihren Ofen wieder instand.</p>
        <p><strong>Inbetriebnahme:</strong><br>Sie haben einen neuen Ofen erworben und möchten sich über die richtige Nutzung und Befeuerung informieren?</p>
        <p><strong>Kaufberatung:</strong><br>Sie planen eine Neuanschaffung und möchten sich vorab über Anschlussmöglichkeiten, Brennstoffarten und Modelle informieren? Wir beraten Sie unabhängig und auf Ihre Bedürfnisse zugeschnitten.</p>
      </div>
    </div>
  </div>

  <div class="panel panel--contact">
    <div class="contact">
      <div class="contact__address">Birkenallee 7<br>35999 Talheim</div>
      <div class="contact__phone">06400 / 555-01-23</div>
    </div>
    <div class="grey-area" style="top:104px;background:var(--paper-soft);padding:14px 16px">
      <p class="copy">Als inhabergeführtes Unternehmen bieten wir professionelle Serviceleistungen rund um Öfen aller Art (Kaminöfen, Pelletöfen, Scheitholzöfen, Kachelöfen, offene Kamine, Grund- und Speicheröfen). Durch erfahrene Mitarbeiter, regelmäßige Personalschulungen und Zusammenarbeit mit namhaften Herstellern können wir Ihnen eine breite Palette an Dienstleistungen rund um Kaminöfen bieten. Guter Service muss nicht teuer sein! Überzeugen Sie sich von unserem Preis-Leistungs-Verhältnis sowie unseren exklusiven Konditionen bei Abschluss eines Wartungsvertrags.</p>
    </div>
  </div>

  <div class="panel panel--cover">
    <svg class="cover-curve" viewBox="0 0 215 250" aria-hidden="true">
      <path d="M0 62 L150 62 Q205 62 215 40 L215 250 L0 250 Z" fill="var(--panel-grey)"/>
    </svg>
    <div class="brand"><span class="brand__mark"></span><span class="brand__name">KALORA</span></div>
    <div class="brand__sub">Ofenservice</div>
    <div class="headline">Kompetenter Servicespezialist<br>für Öfen aller Art</div>
    <ul class="bullets list">
      <li>Wartung von Öfen aller Art</li>
      <li>Reparatur, Inbetriebnahme und Beratung</li>
      <li>Günstige Konditionen</li>
    </ul>
    <div class="photo photo--team" role="img" aria-label="Teamfoto: drei Servicemitarbeiter in schwarzer Arbeitskleidung"></div>
  </div>
</section>

<section class="spread spread--inside" aria-label="Innenseite">
  <div class="panel panel--pellet">
    <div class="photo photo--pellet" role="img" aria-label="Foto: weißer Pelletofen mit Sichtfenster"></div>
    <div class="tab">Pelletöfen</div>
    <div class="copy" style="position:absolute;left:14px;right:12px;top:108px">
      <p><strong>Die Wartung beinhaltet:</strong></p>
      <ul class="list">
        <li>Reinigung von Sichtscheibe, Brenntopf, Topfhalter, Zwischenboden, gesamter Feuerraum, sämtliche Rauchgaszüge und Aschebehälter</li>
        <li>Reinigung des Saugzuggebläses</li>
        <li>Überprüfung und Reinigung des Luftmengensensors</li>
        <li>Überprüfung der elektrischen Zündung</li>
        <li>Überprüfung der Dichtungen (Türdichtung, Türglasdichtung, Putzdeckeldichtungen)</li>
        <li>Überprüfung des Temperaturwächters</li>
        <li>Probelauf des Gerätes</li>
      </ul>
      <p><strong>Preise:</strong><br>Mit Wartungsvertrag: 140€ inkl. MwSt<br>Ohne Wartungsvertrag: 180€ inkl. MwSt</p>
    </div>
  </div>

  <div class="panel panel--wood">
    <div class="photo photo--room" role="img" aria-label="Foto: Scheitholzofen in hellem Wohnraum"></div>
    <div class="type-tags">
      <span>Scheitholzöfen</span><span>Heizkassetten</span><span>Brennzellen</span><span>Holz- und Küchenherde</span>
    </div>
    <div class="copy" style="position:absolute;left:14px;right:12px;top:104px">
      <p><strong>Die Wartung beinhaltet:</strong></p>
      <ul class="list">
        <li>Reinigung Schamott Verkleidung, Sichtscheibe, Zwischenboden, gesamter Feuerraum, sämtliche Rauchgaszüge, Aschebehälter</li>
        <li>Reinigung der Abgasrohre (bis 2 m gestreckte Länge)</li>
        <li>Überprüfung der Dichtungen (Türdichtung, Türglasdichtung, Putzdeckeldichtungen)</li>
        <li>Probelauf des Gerätes</li>
      </ul>
      <p><strong>Preise:</strong><br>Mit Wartungsvertrag: 80€ inkl. MwSt<br>Ohne Wartungsvertrag: 110€ inkl. MwSt</p>
    </div>
    <div class="offer">
      <div class="offer__title">AKTION</div>
      <div class="offer__text">50€ für Neukundenwerbung</div>
      <div class="offer__note">(bei Abschluss eines Wartungsvertrags)</div>
    </div>
  </div>

  <div class="panel panel--tile">
    <div class="photo photo--modern" role="img" aria-label="Foto: moderner Kachelofen mit Feuer im Wohnzimmer"></div>
    <div class="tab">Grund-/Kachelöfen</div>
    <div class="grey-area" style="top:104px;background:var(--paper-soft);padding:8px 12px 0 14px">
      <div class="copy">
        <p><strong>Leistung:</strong></p>
        <ul class="list">
          <li>Reinigung Schamott Verkleidung, Sichtscheibe, Zwischenboden, gesamter Feuerraum, sämtliche Rauchgaszüge, Aschebehälter</li>
          <li>Reinigung der Abgasrohre (bis 2 m gestreckte Länge)</li>
          <li>Überprüfung der Dichtungen (Türdichtung, Türglasdichtung, Putzdeckeldichtungen)</li>
          <li>Probelauf des Gerätes</li>
        </ul>
        <p><strong>Preise Kachelofen mit bis zu 4 Öffnungen</strong><br>Mit Wartungsvertrag: 350€ inkl. MwSt<br>Ohne Wartungsvertrag: 390€ inkl. MwSt</p>
        <p><strong>Preise Kachelofen mit nachgeschalteter Heizfläche</strong><br>Mit Wartungsvertrag: 250€ inkl. MwSt<br>Ohne Wartungsvertrag: 290€ inkl. MwSt</p>
      </div>
    </div>
  </div>
</section>

</body>
</html>
```